Cutting Edge Cloud Hosting Provider needs business card design

We are a new Cloud Hosting Provider called Velkari Hosting. (Velkari means cloudy in Spanish.) We provide clients with virtual resources and not virtual machines directly. Our clients purchase the resources that they will use (RAM,CPU, Hard drive space) then use those resources in as many virtual machines as they like.

We are looking for a business card design that is cutting edge and hip.
Updates

The name of the company is "Velkari Hosting". Please include the "Hosting" part of our name in the design.

Thanks

Target Market(s)

21-35 developers and I.T. Staff

Industry/Entity Type

Business

Requirements
Must have
• Rounded corners, Must Incorporate our logo, individual's name must be prominent

```html
<!DOCTYPE html>
<html lang="en">
<head>
<meta charset="utf-8">
<title>Velkari Hosting – Business Card</title>
<link href="https://fonts.googleapis.com/css2?family=Quicksand:wght@500;600;700&display=swap" rel="stylesheet">
<style>
  :root {
    --backdrop: #3a5382;
    --card-top: #e8edf5;
    --card-bottom: #dfe6f1;
    --band-top: #b8cae4;
    --band-bottom: #cdd9ec;
    --ink-dark: #283d69;
    --ink-mid: #47679e;
    --ink-soft: #4f6ea3;
  }
  * { margin: 0; padding: 0; box-sizing: border-box; }
  html, body { width: 1200px; height: 900px; overflow: hidden; }
  body {
    background: var(--backdrop);
    font-family: "Quicksand", sans-serif;
    position: relative;
  }
  .card {
    position: absolute;
    top: 235px;
    width: 533px;
    height: 300px;
    border-radius: 22px;
    overflow: hidden;
    background: linear-gradient(180deg, var(--card-top), var(--card-bottom));
    box-shadow: 0 6px 18px rgba(10, 25, 60, 0.35);
  }
  .card--front { left: 45px; }
  .card--back { left: 622px; }
  .card__band {
    position: absolute;
    left: 0; right: 0;
    top: 70px;
    bottom: 0;
    background: linear-gradient(180deg, var(--band-top), var(--band-bottom));
  }
  .card__content {
    position: absolute;
    inset: 0;
    text-align: center;
  }
  .brand-name {
    position: absolute;
    left: 0; right: 0;
    top: 78px;
    font-size: 118px;
    font-weight: 600;
    letter-spacing: 2px;
    color: var(--ink-dark);
    line-height: 1;
  }
  .brand-tagline {
    position: absolute;
    left: 0; right: 0;
    top: 205px;
    font-size: 34px;
    font-weight: 600;
    color: var(--ink-mid);
  }
  .person-name {
    position: absolute;
    left: 0; right: 0;
    top: 118px;
    font-size: 58px;
    font-weight: 600;
    letter-spacing: 1px;
    color: var(--ink-dark);
    line-height: 1;
  }
  .person-title {
    position: absolute;
    left: 0; right: 0;
    top: 184px;
    font-size: 23px;
    font-weight: 700;
    color: var(--ink-dark);
  }
  .contact {
    position: absolute;
    left: 0; right: 0;
    top: 218px;
    list-style: none;
    color: var(--ink-soft);
    font-weight: 600;
    line-height: 1.15;
  }
  .contact__email { font-size: 18px; }
  .contact__phone { font-size: 15px; }
</style>
</head>
<body>

  <section class="card card--front" aria-label="Card front">
    <div class="card__band" role="img" aria-label="Decorative cloud border band"></div>
    <div class="card__content">
      <h1 class="brand-name">velkari</h1>
      <p class="brand-tagline">cloud hosting</p>
    </div>
  </section>

  <section class="card card--back" aria-label="Card back">
    <div class="card__band" role="img" aria-label="Decorative cloud border band"></div>
    <div class="card__content">
      <h2 class="person-name">marco ibarra</h2>
      <p class="person-title">vice president</p>
      <ul class="contact">
        <li class="contact__email">marco (at) velkari.com</li>
        <li class="contact__phone">p: 210 · 555 · 0142</li>
        <li class="contact__phone">c: 210 · 555 · 0187</li>
      </ul>
    </div>
  </section>

</body>
</html>
```